VL Business Card

Used Car Sales
We are trying to recreate the image of our license plate on business cards,
it is a red background with a white oval that is open on the ends
I attempted to upload the image but it was a dismal failure when the products arrived
the lettering was too small and the edges were white
I think maybe the red needs some texture in it, still red but something that doesn't look so flat
and maybe a beveled edge around the white (not sure)

Target Market(s)

Adults 25-65 that drive

Industry/Entity Type

Business

Contact Information for Business Card

Danielle Hargrove, Sales Manager, FAIRVIEW AUTO SALES, INC., 462 Birch Lane, Pulaski, TN 38491,
931 555-0172 (office), 931 555-0186 (fax) - We Finance everyone with approved credit
FairviewAutoSales.Example

On Back: Financing Available - We Finance everyone with approved credit
Easy Payments: Monthly, Semi-Monthly or Weekly
Ask about our Layaway plan
Open Mon-Sat
8:30 AM - 5 PM

Requirements
Must have
• We want to match the license plate (minus holes for screws)

```html
<!DOCTYPE html>
<html lang="en">
<head>
<meta charset="utf-8">
<title>VL Business Card</title>
<link rel="stylesheet" href="https://fonts.googleapis.com/css2?family=Rubik:ital,wght@0,400;0,500;0,700;0,800;1,400;1,700&display=swap">
<style>
  :root {
    --plate-red: #e8262a;
    --plate-red-deep: #c8161c;
    --plate-red-light: #f5413a;
    --panel-white: #ffffff;
    --ink: #1c1c1c;
    --accent: #e31e24;
    --backdrop: #e9e9ec;
  }
  * { box-sizing: border-box; margin: 0; padding: 0; }
  html, body { width: 1200px; height: 1000px; overflow: hidden; }
  body {
    background: var(--backdrop);
    font-family: "Rubik", Arial, sans-serif;
    color: var(--ink);
    display: flex;
    flex-direction: column;
    align-items: center;
    justify-content: center;
    gap: 60px;
  }
  .card {
    position: relative;
    width: 700px;
    height: 400px;
    border-radius: 6px;
    background:
      linear-gradient(135deg, var(--plate-red-deep) 0%, var(--plate-red) 35%, var(--plate-red-light) 55%, var(--plate-red) 75%, var(--plate-red-deep) 100%);
    box-shadow: 0 10px 26px rgba(0,0,0,0.18);
  }
  .plate-panel {
    position: absolute;
    inset: 40px 42px;
    background: var(--panel-white);
    border-radius: 38px;
    box-shadow: inset 0 0 0 2px rgba(0,0,0,0.06), 0 2px 4px rgba(0,0,0,0.2);
    display: flex;
    flex-direction: column;
    align-items: center;
    justify-content: center;
    text-align: center;
    line-height: 1.15;
  }
  .holder-name {
    color: var(--accent);
    font-weight: 700;
    font-size: 40px;
    letter-spacing: 0.5px;
  }
  .holder-title {
    font-weight: 700;
    font-size: 22px;
    margin-top: 2px;
  }
  .divider { display: block; margin: 6px 0 4px; }
  .company-name {
    color: var(--accent);
    font-weight: 700;
    font-size: 38px;
    letter-spacing: 0.3px;
  }
  .address, .phones {
    font-size: 20px;
    font-weight: 400;
    margin-top: 4px;
  }
  .tagline {
    font-size: 16px;
    font-style: italic;
    margin-top: 4px;
  }
  .website {
    font-weight: 800;
    font-size: 22px;
    margin-top: 6px;
  }
  .back .plate-panel { line-height: 1.25; }
  .back-heading {
    color: var(--accent);
    font-weight: 700;
    font-size: 40px;
  }
  .back-line { font-size: 23px; margin-top: 4px; }
  .back-line.emphasis { font-weight: 700; font-style: italic; margin-top: 10px; }
  .back-line.strong { font-weight: 700; }
  .hours {
    color: var(--accent);
    font-weight: 700;
    font-style: italic;
    font-size: 23px;
    margin-top: 12px;
  }
</style>
</head>
<body>

  <section class="card front">
    <div class="plate-panel">
      <div class="holder-name">DANIELLE HARGROVE</div>
      <div class="holder-title">Sales Manager</div>
      <svg class="divider" width="300" height="8" viewBox="0 0 300 8" aria-hidden="true">
        <line x1="4" y1="4" x2="296" y2="4" stroke="var(--accent)" stroke-width="1"/>
        <circle cx="4" cy="4" r="3" fill="var(--accent)"/>
        <circle cx="296" cy="4" r="3" fill="var(--accent)"/>
      </svg>
      <div class="company-name">FAIRVIEW AUTO SALES, INC.</div>
      <div class="address">462 Birch Lane, Pulaski, TN 38491</div>
      <div class="phones">Office: 931 555-0172 &bull; Fax: 931 555-0186</div>
      <div class="tagline">We Finance everyone with approved credit</div>
      <div class="website">FairviewAutoSales.Example</div>
    </div>
  </section>

  <section class="card back">
    <div class="plate-panel">
      <div class="back-heading">Financing Available</div>
      <div class="back-line">We Finance everyone with approved credit</div>
      <div class="back-line emphasis">Easy Payments:</div>
      <div class="back-line">Monthly, Semi-Monthly or Weekly</div>
      <div class="back-line strong">Ask about our Layaway plan</div>
      <div class="hours">Open Mon-Sat &bull; 8:30 AM - 5 PM</div>
    </div>
  </section>

</body>
</html>
```